New Webpage for High Class Expert Witness Services Company

We are looking for a minimalist design for a webpage that just has our logo and an entry form offer to connect with one of our Liaisons.
The entry form should just ask for Name, Email, Contact Info and Description of Project.

Company Name is: The Marlowe Crest Advisory Services

Number of Pages Required

1 page

```html
<!DOCTYPE html>
<html lang="en">
<head>
<meta charset="UTF-8">
<title>The Marlowe Crest Advisory Services</title>
<link rel="stylesheet" href="https://fonts.googleapis.com/css2?family=Cinzel:wght@500;600&family=Poppins:wght@400;500;600&display=swap">
<style>
:root{
  --hero-dark:#2a2d33;
  --form-bg:#1f2023;
  --form-border:#9a9ca0;
  --accent:#fb9400;
  --white:#ffffff;
  --ink:#2c2c2c;
  --body:#3a3a3a;
  --grey-card:#ececec;
  --button-top:#f1f1f1;
  --button-bottom:#b9b9b9;
  --footer:#2a2a2a;
  --footer-text:#e6e6e6;
}
*{box-sizing:border-box;margin:0;padding:0}
html,body{width:1039px;height:1200px;overflow:hidden}
body{font-family:"Poppins",sans-serif;color:var(--body);background:var(--white);position:relative}

.hero{position:absolute;left:0;top:0;width:1039px;height:565px;overflow:hidden}
.hero-photo{position:absolute;inset:0;background:
  radial-gradient(ellipse at 48% 40%, #6d7278 0%, transparent 55%),
  linear-gradient(100deg,#2d3035 0%,#4b5057 45%,#3c4147 70%,#2a2d31 100%)}
.hero-shade{position:absolute;inset:0;background:rgba(30,33,38,.35)}

.brand{position:absolute;left:0;right:0;display:flex;justify-content:center;color:var(--white)}
.brand-name{font-family:"Cinzel",serif;font-weight:600;letter-spacing:.5px;line-height:1;display:flex;align-items:center;gap:12px}
.brand-mark{background:var(--white);flex:none}
.hero .brand{top:58px}
.hero .brand-name{font-size:30px}
.hero .brand-mark{width:16px;height:16px}

.hero-copy{position:absolute;left:64px;top:226px;color:var(--white)}
.hero-title{font-family:"Cinzel",serif;font-weight:500;line-height:1.06}
.hero-title .lead{display:block;font-size:30px}
.hero-title .main{display:block;font-size:39px}
.hero-sub{font-weight:600;font-size:21.5px;margin-top:10px;letter-spacing:.2px}
.btn{display:inline-flex;align-items:center;justify-content:center;width:130px;height:40px;
  background:linear-gradient(var(--button-top),var(--button-bottom));
  font-family:"Cinzel",serif;font-weight:600;font-size:13.5px;color:var(--ink);letter-spacing:.5px;border-radius:2px;text-decoration:none}
.hero-copy .btn{margin-top:17px;margin-left:2px}

.liaison-form{position:absolute;left:688px;top:139px;width:287px;height:383px;background:var(--form-bg);border:2px solid var(--form-border);padding:14px 16px 0 15px}
.liaison-form h2{font-family:"Cinzel",serif;font-weight:600;color:var(--accent);font-size:26px;line-height:1;margin-bottom:12px}
.field{display:flex;align-items:center;background:var(--white);border-radius:2px;height:42px;padding:0 12px;font-size:11.5px;color:#222;margin-bottom:8px}
.field.area{height:83px;align-items:flex-start;padding-top:12px}
.submit{display:flex;align-items:center;justify-content:center;height:43px;background:var(--accent);color:var(--white);font-family:"Cinzel",serif;font-weight:600;font-size:15px;letter-spacing:.5px;border-radius:2px}

.about-card{position:absolute;left:65px;top:624px;width:283px;height:259px;background:var(--grey-card);border-radius:12px}
.about-photo{position:absolute;left:80px;top:638px;width:417px;height:351px;background:linear-gradient(120deg,#c9d2d6 0%,#a8b0ad 50%,#8a8d7d 100%)}
.about-copy{position:absolute;left:533px;top:620px;width:445px}
.about-copy h2{font-family:"Cinzel",serif;font-weight:600;font-size:33px;line-height:1.04;color:var(--ink);letter-spacing:.3px}
.about-copy p{font-size:13.3px;line-height:23.5px;margin-top:14px;color:var(--body)}
.about-copy p + p{margin-top:8px}
.about-copy .btn{margin-top:26px}

.site-footer{position:absolute;left:0;top:1073px;width:1039px;height:127px;background:var(--footer);color:var(--footer-text)}
.copyright{position:absolute;left:79px;top:68px;font-size:10px}
.site-footer .brand{top:56px}
.site-footer .brand-name{font-size:23px}
.site-footer .brand-mark{width:12px;height:12px}
.social{position:absolute;right:64px;top:55px;display:flex;gap:18px;list-style:none}
.social li{width:22px;height:22px;border-radius:50%;border:2px solid var(--footer-text)}
.scale-note{position:absolute;right:6px;bottom:4px;font-size:9px;color:#bbb}
</style>
</head>
<body>
<header class="hero">
  <div class="hero-photo" role="img" aria-label="Physician in white coat with stethoscope working at a desk"></div>
  <div class="hero-shade"></div>
  <div class="brand">
    <div class="brand-name"><span class="brand-mark"></span>MARLOWE CREST ADVISORY</div>
  </div>
  <div class="hero-copy">
    <h1 class="hero-title"><span class="lead">Welcome to</span><span class="main">The Marlowe Crest</span><span class="main">Advisory Services</span></h1>
    <p class="hero-sub">Seamless Medical Expert Integration</p>
    <a class="btn" href="#about">Learn More</a>
  </div>
  <form class="liaison-form">
    <h2>Connect With<br>A Liaison</h2>
    <div class="field">Name</div>
    <div class="field">Email Address</div>
    <div class="field">Contact No</div>
    <div class="field area">Description of Project</div>
    <div class="submit">Submit Now</div>
  </form>
</header>

<section id="about">
  <div class="about-card"></div>
  <div class="about-photo" role="img" aria-label="Military medical professional in camouflage uniform with stethoscope in a clinic"></div>
  <div class="about-copy">
    <h2>About The Marlowe Crest Advisory Services</h2>
    <p>Sed ut perspiciatis unde omnis iste natus error sit voluptatem accusantium doloremque laudantium, totam rem aperiam, eaque ipsa quae ab illo inventore veritatis et quasi architecto beatae vitae dicta sunt explicabo. Nemo enim ipsam voluptatem quia voluptas sit aspernatur aut odit aut fugit, sed quia consequuntur magni dolores eos qui ratione voluptatem sequi nesciunt.</p>
    <p>Sed ut perspiciatis unde omnis iste natus error sit voluptatem accusantium doloremque laudantium, totam rem aperiam, eaque ipsa quae ab illo inventore veritatis.</p>
    <a class="btn" href="#">Learn More</a>
  </div>
</section>

<footer class="site-footer">
  <p class="copyright">© 2026 Company Name&nbsp; All Rights Reserved</p>
  <div class="brand">
    <div class="brand-name"><span class="brand-mark"></span>MARLOWE CREST ADVISORY</div>
  </div>
  <ul class="social" aria-label="Social links">
    <li aria-label="Social link 1"></li>
    <li aria-label="Social link 2"></li>
    <li aria-label="Social link 3"></li>
    <li aria-label="Social link 4"></li>
  </ul>
  <span class="scale-note">x10</span>
</footer>
</body>
</html>
```